Birchline Septic Solutions

Would like to see some single sided ones but would also like to see some double sided with one sided only being the logo. Owners name is Colin Vandro. Phone number is 555-214-0387
Services are pumping, inspections, installs, and repairs

Contact Information for Business Card

555-241-0387 Colin Vandro Maplewood, OH

```html
<!DOCTYPE html>
<html lang="en">
<head>
<meta charset="utf-8">
<title>Birchline Septic Solutions — Business Cards</title>
<link rel="stylesheet" href="https://fonts.googleapis.com/css2?family=Open+Sans:wght@400;600;700;800&display=swap">
<style>
  :root {
    --backdrop: #232325;
    --card: #232428;
    --teal: #2bbab0;
    --white: #ffffff;
    --muted-art: #2e3034;
    --emboss: #141416;
  }
  * { box-sizing: border-box; margin: 0; padding: 0; }
  html, body {
    width: 1200px; height: 779px; overflow: hidden;
    background: var(--backdrop);
    font-family: "Open Sans", Arial, sans-serif;
  }
  .canvas {
    position: relative; width: 1200px; height: 779px;
    display: flex; align-items: center; justify-content: center; gap: 40px;
  }
  .card {
    position: relative; width: 540px; height: 309px;
    background: var(--card);
    border: 3px solid var(--teal);
    border-radius: 18px;
    overflow: hidden;
  }

  /* Logo-only side */
  .card--logo { display: flex; align-items: center; justify-content: center; }
  .logo-mark { display: flex; align-items: center; gap: 14px; color: var(--emboss); }
  .logo-mark__dot { width: 26px; height: 26px; border-radius: 50%; background: var(--emboss); flex: none; }
  .logo-mark__name {
    font-weight: 800; font-size: 30px; line-height: 1.1; letter-spacing: 0.5px;
    text-transform: uppercase; max-width: 300px;
  }

  /* Contact side */
  .scenery {
    position: absolute; left: 90px; right: 0; top: 40px; bottom: 80px;
    background: linear-gradient(180deg, rgba(46,48,52,0) 0%, var(--muted-art) 55%, rgba(46,48,52,0.4) 100%);
  }
  .brand {
    position: absolute; left: 60px; top: 110px;
    display: flex; align-items: center; gap: 10px;
  }
  .brand__dot { width: 14px; height: 14px; background: var(--teal); border-radius: 50%; flex: none; }
  .brand__name {
    color: var(--white); font-weight: 800; font-size: 20px; line-height: 1.15;
    text-transform: uppercase; max-width: 170px;
  }
  .divider {
    position: absolute; left: 262px; top: 48px; width: 1.5px; height: 150px;
    background: var(--white);
  }
  .contact { position: absolute; left: 290px; top: 70px; color: var(--white); }
  .contact__name { font-size: 28px; font-weight: 700; line-height: 1.1; }
  .contact__first { color: var(--teal); }
  .contact__line { font-size: 15px; line-height: 1.5; margin-top: 4px; }
  .contact__phone { display: flex; align-items: center; gap: 8px; }
  .contact__phone svg { width: 14px; height: 14px; }

  .services {
    position: absolute; left: 0; right: 0; bottom: 22px;
    display: flex; flex-direction: column; align-items: center; gap: 6px;
  }
  .services__tag {
    align-self: center; margin-left: 60px;
    background: var(--teal); color: var(--white);
    font-weight: 600; font-size: 13px; letter-spacing: 0.5px; line-height: 1;
    padding: 5px 16px; border-radius: 50%;
  }
  .services__list {
    list-style: none;
    display: flex; justify-content: center; align-items: center; gap: 12px;
    color: var(--white); font-size: 15px;
  }
  .services__item { display: flex; align-items: center; gap: 6px; }
  .services__item::before {
    content: ""; width: 9px; height: 9px; border-radius: 50%; background: var(--teal);
  }
</style>
</head>
<body>
<main class="canvas">
  <section class="card card--logo" aria-label="Card front, logo only">
    <div class="logo-mark">
      <span class="logo-mark__dot"></span>
      <span class="logo-mark__name">Birchline Septic Solutions</span>
    </div>
  </section>

  <section class="card card--contact" aria-label="Card back, contact details">
    <div class="scenery" role="img" aria-label="Faint mountain peak and pine forest silhouette"></div>
    <div class="brand">
      <span class="brand__dot"></span>
      <span class="brand__name">Birchline Septic Solutions</span>
    </div>
    <div class="divider"></div>
    <div class="contact">
      <p class="contact__name"><span class="contact__first">Colin</span> Vandro</p>
      <p class="contact__line">Maplewood, OH</p>
      <p class="contact__line contact__phone">
        <svg viewBox="0 0 24 24" aria-hidden="true"><path fill="var(--teal)" d="M6.6 10.8a15.1 15.1 0 0 0 6.6 6.6l2.2-2.2a1 1 0 0 1 1-.25 11.4 11.4 0 0 0 3.6.57 1 1 0 0 1 1 1V20a1 1 0 0 1-1 1A17 17 0 0 1 3 4a1 1 0 0 1 1-1h3.5a1 1 0 0 1 1 1c0 1.25.2 2.45.57 3.6a1 1 0 0 1-.25 1z"/></svg>
        555-241-0387
      </p>
    </div>
    <div class="services">
      <span class="services__tag">SERVICES</span>
      <ul class="services__list" aria-label="Services">
        <li class="services__item">Pumping</li>
        <li class="services__item">Inspections</li>
        <li class="services__item">Installs</li>
        <li class="services__item">And Repairs</li>
      </ul>
    </div>
  </section>
</main>
</body>
</html>
```